Business Card Design for Marketing Firm

Looking for business card design for higher end marketing firm. Clean but impressionable/trendy. We are a marketing firm that represents manufacturers in the foodservice equipment and supply industry. Our customers are end users such has hotels, restaurants, country clubs, convention centers and casinos as well as distributors of restaurants supplies and equipment, and manufacturers of foodservice equipment and supplies.
Target Market(s)
Hotels, Restaurants, Supply & Equipment Distributors, Foodservice Manufacturers
Industry/Entity Type
Foodservice/Hospitality
Contact Information for Business Card
Name, Title, Contact Number, Email, Website, Social Media, Address
Requirements
Must have
- Clean & Simple but Serious and Impressionable

```html
<!DOCTYPE html>
<html lang="en">
<head>
<meta charset="utf-8">
<title>Meridian Service Reps – Business Card</title>
<link rel="stylesheet" href="https://fonts.googleapis.com/css2?family=Montserrat:wght@500;600;800&display=swap">
<style>
  :root {
    --navy: #2b2880;
    --navy-deep: #232070;
    --navy-light: #35339a;
    --white: #ffffff;
    --ink: #1c1c24;
    --stage: #2c2c2e;
  }
  * { margin: 0; padding: 0; box-sizing: border-box; }
  html, body { width: 1200px; height: 960px; overflow: hidden; background: var(--stage); }
  .canvas {
    width: 1200px; height: 960px;
    display: flex; flex-direction: column; align-items: center; justify-content: center; gap: 60px;
  }
  .card { position: relative; width: 700px; height: 400px; border-radius: 26px; overflow: hidden; }
  .card--front { background: linear-gradient(135deg, var(--navy-light) 0%, var(--navy) 50%, var(--navy-deep) 100%); }
  .card--back { background: var(--white); }

  .brand {
    position: absolute; display: flex; align-items: center;
    font-family: "Montserrat", sans-serif; font-weight: 600; text-transform: uppercase; letter-spacing: 0.06em;
  }
  .brand__mark { border-radius: 50%; flex: none; }
  .brand__name { line-height: 1.15; }

  .card--front .brand { left: 0; right: 0; top: 0; bottom: 0; justify-content: center; gap: 26px; color: var(--white); }
  .card--front .brand__mark { width: 72px; height: 72px; background: var(--white); }
  .card--front .brand__name { font-size: 34px; }

  .card--back .brand { left: 40px; top: 112px; gap: 16px; color: var(--navy); }
  .card--back .brand__mark { width: 44px; height: 44px; background: var(--navy); }
  .card--back .brand__name { font-size: 20px; }

  .divider { position: absolute; left: 345px; top: 42px; width: 2px; height: 200px; background: var(--navy); }

  .contact { position: absolute; left: 368px; top: 30px; font-family: "Montserrat", sans-serif; color: var(--ink); }
  .contact__name { font-weight: 800; font-size: 21px; color: var(--navy); letter-spacing: 0.01em; }
  .contact__title { font-weight: 500; font-size: 13px; margin-top: 2px; }
  .contact__address { font-weight: 500; font-size: 13px; line-height: 1.4; margin-top: 10px; }
  .contact__list { list-style: none; margin-top: 10px; }
  .contact__item { display: flex; align-items: center; gap: 8px; font-weight: 500; font-size: 13px; height: 22px; }
  .contact__icon { width: 14px; height: 14px; flex: none; }
  .contact__dot { width: 12px; height: 12px; border-radius: 50%; background: var(--navy); flex: none; margin: 0 1px; }

  .wave { position: absolute; inset: 0; }
</style>
</head>
<body>
<main class="canvas">
  <section class="card card--front" aria-label="Card front">
    <div class="brand">
      <span class="brand__mark"></span>
      <span class="brand__name">Meridian Service<br>Reps</span>
    </div>
  </section>

  <section class="card card--back" aria-label="Card back">
    <svg class="wave" viewBox="0 0 700 400" width="700" height="400" aria-hidden="true">
      <path d="M0,400 L0,362 C200,352 330,328 440,278 C540,232 610,222 700,214 L700,400 Z" fill="var(--navy)"/>
      <path d="M70,348 C240,336 340,314 434,266 C528,218 600,206 680,200" fill="none" stroke="var(--navy)" stroke-width="3"/>
    </svg>

    <div class="brand">
      <span class="brand__mark"></span>
      <span class="brand__name">Meridian Service<br>Reps</span>
    </div>

    <div class="divider"></div>

    <div class="contact">
      <div class="contact__name">DANIEL HARTWELL</div>
      <div class="contact__title">Co-Founder</div>
      <div class="contact__address">P.O. BOX 40-12 NTH-55<br>Linden St 14, Fairview</div>
      <ul class="contact__list">
        <li class="contact__item">
          <svg class="contact__icon" viewBox="0 0 16 16"><path d="M3 2h3l1.5 3.5-2 1.2a8 8 0 0 0 3.8 3.8l1.2-2L14 10v3a1 1 0 0 1-1 1A11 11 0 0 1 2 3a1 1 0 0 1 1-1z" fill="var(--navy)"/></svg>
          555-014-2290
        </li>
        <li class="contact__item">
          <svg class="contact__icon" viewBox="0 0 16 16"><rect x="1" y="3" width="14" height="10" rx="1" fill="var(--navy)"/><path d="M1.5 4l6.5 5 6.5-5" fill="none" stroke="var(--white)" stroke-width="1.3"/></svg>
          hello@meridianservice.com
        </li>
        <li class="contact__item">
          <svg class="contact__icon" viewBox="0 0 16 16"><circle cx="8" cy="8" r="6.5" fill="none" stroke="var(--navy)" stroke-width="1.5"/><ellipse cx="8" cy="8" rx="2.8" ry="6.5" fill="none" stroke="var(--navy)" stroke-width="1.2"/><path d="M1.5 8h13" stroke="var(--navy)" stroke-width="1.2"/></svg>
          www.meridianservice.com
        </li>
        <li class="contact__item">
          <span class="contact__dot"></span>
          @meridianservice
        </li>
      </ul>
    </div>
  </section>
</main>
</body>
</html>
```